Upmarket Dessert Lounge needs a Business Card Design

We are an upmarket dessert lounge needing a business card to match our image.

We want something that is simple yet beautiful, feminine, classy, sophisticated and elegant. We want it to stand out and don't mind if it is bold.

The design should include our logo and colours of red or maroon with gold highlights. We don't mind if black is used.

Marlow & Quince

Target Market(s)

For those who like to indulge or treat themselves and give in to their temptations on good quality desserts.

Industry/Entity Type

Business

Requirements
Must have
• Must include our logo and our name

Marlow & Quince

M & Q

```html
<!DOCTYPE html>
<html lang="en">
<head>
<meta charset="utf-8">
<title>Marlow &amp; Quince — Business Card</title>
<link rel="stylesheet" href="https://fonts.googleapis.com/css2?family=Cinzel:wght@500&family=Libre+Baskerville:wght@700&family=Open+Sans:wght@400;600&display=swap">
<style>
  :root {
    --maroon: #7e1a1a;
    --maroon-light: #a52a24;
    --maroon-deep: #5a0f10;
    --gold: #e9b67c;
    --gold-soft: #f3c894;
    --ink: #3a3a3a;
    --paper: #ffffff;
    --backdrop: #e9e6e3;
  }
  * { box-sizing: border-box; margin: 0; padding: 0; }
  html, body { width: 1200px; height: 951px; overflow: hidden; }
  body { background: var(--backdrop); position: relative; }

  .card {
    position: absolute;
    width: 700px;
    height: 400px;
    border-radius: 22px;
    overflow: hidden;
    box-shadow: 0 10px 28px rgba(0,0,0,.22);
  }

  /* Front */
  .card-front {
    left: 60px; top: 50px;
    background: radial-gradient(ellipse at 40% 45%, var(--maroon-light) 0%, var(--maroon) 55%, var(--maroon-deep) 100%);
  }
  .card-front .flourish {
    position: absolute; right: 0; top: 0;
    width: 380px; height: 110px;
    background: radial-gradient(ellipse at 60% 30%, rgba(233,182,124,.55), rgba(233,182,124,0) 70%);
  }
  .card-front .brand-name {
    position: absolute; left: 0; right: 0; top: 160px;
    text-align: center;
    font-family: "Cinzel", serif;
    font-weight: 500;
    font-size: 46px;
    letter-spacing: 1px;
    color: var(--gold);
  }
  .card-front .website {
    position: absolute; left: 150px; bottom: 48px;
    font-family: "Libre Baskerville", serif;
    font-weight: 700;
    font-size: 18px;
    color: var(--paper);
    letter-spacing: .5px;
  }

  /* Back */
  .card-back {
    left: 440px; top: 501px;
    background: var(--paper);
  }
  .card-back .swoosh { position: absolute; inset: 0; }
  .card-back .brand-name {
    position: absolute; left: 60px; top: 52px; width: 300px;
    text-align: center;
    font-family: "Cinzel", serif;
    font-weight: 500;
    font-size: 30px;
    color: var(--maroon);
  }
  .contact-list {
    position: absolute; left: 28px; top: 218px;
    list-style: none;
    font-family: "Open Sans", sans-serif;
    font-size: 19px;
    color: var(--ink);
    line-height: 26px;
  }
  .contact-list li { display: flex; align-items: center; gap: 10px; }
  .contact-list svg { width: 17px; height: 17px; flex: none; }
  .signature {
    position: absolute; right: 40px; bottom: 38px;
    font-family: "Open Sans", sans-serif;
    font-weight: 600;
    font-size: 26px;
    color: var(--maroon);
  }
  .signature .amp { color: var(--gold); }
</style>
</head>
<body>

<section class="card card-front">
  <div class="flourish" role="img" aria-label="Gold floral flourish ornament"></div>
  <div class="brand-name">Marlow &amp; Quince</div>
  <div class="website">www.marlowquince.com</div>
</section>

<section class="card card-back">
  <svg class="swoosh" viewBox="0 0 700 400" aria-hidden="true">
    <defs>
      <linearGradient id="swooshRed" x1="0" y1="0" x2="1" y2="1">
        <stop offset="0" stop-color="#a52a24"/>
        <stop offset="1" stop-color="#6e1414"/>
      </linearGradient>
    </defs>
    <path d="M300,0 C500,15 640,130 700,330 L700,0 Z" fill="var(--gold-soft)"/>
    <path d="M390,0 C550,25 660,130 700,240 L700,0 Z" fill="url(#swooshRed)"/>
    <path d="M540,45 C610,85 665,150 700,215 L700,195 C665,135 615,80 540,45 Z" fill="var(--gold)"/>
  </svg>

  <div class="brand-name">Marlow &amp; Quince</div>

  <ul class="contact-list">
    <li>
      <svg viewBox="0 0 24 24"><path fill="var(--maroon)" d="M6.6 10.8a15 15 0 0 0 6.6 6.6l2.2-2.2a1 1 0 0 1 1-.25 11 11 0 0 0 3.6.6 1 1 0 0 1 1 1V20a1 1 0 0 1-1 1A17 17 0 0 1 3 4a1 1 0 0 1 1-1h3.5a1 1 0 0 1 1 1 11 11 0 0 0 .6 3.6 1 1 0 0 1-.25 1z"/></svg>
      555-014-2200
    </li>
    <li>
      <svg viewBox="0 0 24 24"><rect x="6" y="2" width="12" height="20" rx="2" fill="var(--maroon)"/><rect x="8" y="5" width="8" height="12" fill="#fff"/></svg>
      555-014-2201
    </li>
    <li>
      <svg viewBox="0 0 24 24"><rect x="2" y="5" width="20" height="14" rx="2" fill="var(--maroon)"/><path d="M3 6l9 7 9-7" stroke="#fff" stroke-width="1.6" fill="none"/></svg>
      info@marlowquince.com
    </li>
    <li>
      <svg viewBox="0 0 24 24"><circle cx="12" cy="12" r="10" fill="var(--maroon)"/></svg>
      www.marlowquince.com
    </li>
  </ul>

  <div class="signature">Marlow <span class="amp">&amp;</span> Quince</div>
</section>

</body>
</html>
```